Email design required

We need a design for a paid B2B email campaign and facebook / retargeting banner ads that match the same style.

Website: http://pelmora.staging.hostvantry.com/
Campaign Name: KEX Weariness
Example: http://liftmarrowsites.com/kex-weariness/
- I made this over the weekend. It has the right words, but the style / layout needs to change

Size: 600 pixels wide, no limit on length

Formatting:
Format CSS inline only - This will ensure that size, font family, colour, line height, etc. will all remain the same once it is dropped into our newsletter sending software. See below as an

example,

Here's a mockup of

Target Market(s)

Canadian mortgage brokers

Industry/Entity Type

Campaign

Font styles to use
Sans Serif

Colors
3277b5

Requirements
Must have
• Text from my website example http://liftmarrowsites.com/kex-weariness/
• Otherwise, do whatever you think would look good.

```html
<!DOCTYPE html>
<html lang="en">
<head>
<meta charset="utf-8">
<title>Pelmora – KEX Weariness Email Style Options</title>
<link href="https://fonts.googleapis.com/css2?family=Open+Sans:wght@400;600;700&display=swap" rel="stylesheet">
<style>
  :root{
    --board:#2a2a2b;
    --band:#7b7e73;
    --title-grey:#8d8d8d;
    --label-green:#b4f01e;
    --brand-blue:#3277b5;
    --logo-blue:#1d63ad;
    --headline:#6a5b56;
    --body-text:#555;
    --muted:#777;
    --orange:#f7941d;
    --footer-dark:#434356;
    --header-white:#f7f7f7;
    --grad-a:#d4e5f6;
    --grad-b:#ecf3fb;
    --grad-c:#e2edf9;
  }
  *{box-sizing:border-box;margin:0;padding:0}
  html,body{width:1200px;height:1200px;overflow:hidden}
  body{background:var(--board);font-family:"Open Sans",Arial,sans-serif;position:relative}

  .board-title{position:absolute;left:0;width:1200px;text-align:center;color:var(--title-grey);font-weight:700;font-size:24px;letter-spacing:.3px}
  .board-title.line-1{top:10px}
  .board-title.line-2{top:52px}

  .section-band{position:absolute;left:0;width:1200px;height:61px;background:var(--band);color:#fff;font-weight:700;font-size:23px;display:flex;align-items:center;justify-content:center;letter-spacing:.3px}

  .option-label{position:absolute;color:var(--label-green);font-weight:700;font-size:24px;white-space:nowrap;transform:translateX(-50%)}

  /* Email hero card, built at 480px wide */
  .email-hero{position:absolute;width:480px;height:266px;overflow:hidden;transform-origin:0 0;
    background:linear-gradient(165deg,var(--grad-a) 0%,var(--grad-b) 55%,var(--grad-c) 100%)}
  .email-hero.is-small{height:272px;transform:scale(.805)}
  .email-hero .top-bar{position:absolute;left:0;top:0;width:100%;height:61px}
  .email-hero.has-white-layer .top-bar{background:var(--header-white)}
  .brand{position:absolute;left:22px;top:20px;display:flex;align-items:center;gap:4px;color:var(--logo-blue);font-weight:600;font-size:20px}
  .brand-mark{width:14px;height:14px;background:var(--logo-blue)}
  .contact-link{position:absolute;right:29px;top:30px;font-size:11.5px;color:var(--muted)}
  .headline{position:absolute;left:0;width:100%;top:66px;text-align:center;font-weight:700;font-size:30px;color:var(--headline)}
  .offer{position:absolute;left:10px;width:258px;top:140px;text-align:center;font-size:12.5px;line-height:16px;color:var(--body-text);font-weight:600}
  .offer .price{color:var(--orange)}
  .cta{position:absolute;left:58px;top:190px;width:144px;height:34px;border-radius:17px;background:var(--orange);color:#fff;font-weight:700;font-size:12px;display:flex;align-items:center;justify-content:center;letter-spacing:.2px}
  .hero-art{position:absolute;left:272px;top:123px;width:154px;height:120px;border-radius:8px;background:#fff}
  .hero-art.is-orange{background:var(--orange)}
  .hero-art.has-shadow{box-shadow:3px 4px 6px rgba(0,0,0,.35)}

  /* Footer blocks */
  .email-footer{position:absolute;width:482px;background:#fff}
  .email-footer .about-bar{height:39px;background:var(--brand-blue);color:#fff;font-weight:700;font-size:14px;display:flex;align-items:center;justify-content:center}
  .email-footer .about-body{position:relative}
  .email-footer .about-text{font-size:10.4px;line-height:16px;color:#666}
  .email-footer .legal-bar{height:38px;background:var(--footer-dark);color:#fff;font-size:10.5px;display:flex;align-items:center;justify-content:space-between;padding:0 26px 0 23px}
  .footer-plain .about-body{height:86px}
  .footer-plain .about-text{position:absolute;left:34px;top:10px;width:415px}
  .footer-with-image .about-body{height:120px}
  .footer-with-image .about-art{position:absolute;left:37px;top:14px;width:128px;height:90px;background:linear-gradient(160deg,#3c5a86,#24406b)}
  .footer-with-image .about-text{position:absolute;left:198px;top:9px;width:254px}
</style>
</head>
<body>

  <div class="board-title line-1">DESIGN IDEAS of various Individual Elements</div>
  <div class="board-title line-2">CLIENT Changes To Design&nbsp; # 11527444</div>

  <!-- Image style -->
  <div class="section-band" style="top:99px">CHOOSE IMAGE STYLE</div>
  <div class="option-label" style="left:187px;top:175px">01 - Original Image</div>
  <div class="option-label" style="left:596px;top:175px">02 - Color Image</div>
  <div class="option-label" style="left:1000px;top:175px">03 -&nbsp; Image With Shadow</div>

  <div class="email-hero is-small" style="left:7px;top:230px">
    <div class="top-bar"></div>
    <div class="brand"><span class="brand-mark"></span>Pelmora</div>
    <div class="contact-link">Contact</div>
    <div class="headline">Experiencing KEX Weariness?</div>
    <div class="offer">Unlimited Notice of Assessment Orders<br>For Just <span class="price">$29 / Month</span></div>
    <div class="cta">Get Started Now</div>
    <div class="hero-art" role="img" aria-label="White illustration of a tired worker slumped over a desk"></div>
  </div>

  <div class="email-hero is-small" style="left:404px;top:232px">
    <div class="top-bar"></div>
    <div class="brand"><span class="brand-mark"></span>Pelmora</div>
    <div class="contact-link">Contact</div>
    <div class="headline">Experiencing KEX Weariness?</div>
    <div class="offer">Unlimited Notice of Assessment Orders<br>For Just <span class="price">$29 / Month</span></div>
    <div class="cta">Get Started Now</div>
    <div class="hero-art is-orange" role="img" aria-label="Orange illustration of a tired worker slumped over a desk"></div>
  </div>

  <div class="email-hero is-small" style="left:811px;top:232px">
    <div class="top-bar"></div>
    <div class="brand"><span class="brand-mark"></span>Pelmora</div>
    <div class="contact-link">Contact</div>
    <div class="headline">Experiencing KEX Weariness?</div>
    <div class="offer">Unlimited Notice of Assessment Orders<br>For Just <span class="price">$29 / Month</span></div>
    <div class="cta">Get Started Now</div>
    <div class="hero-art has-shadow" role="img" aria-label="White illustration with drop shadow of a tired worker slumped over a desk"></div>
  </div>

  <!-- Header style -->
  <div class="section-band" style="top:483px">CHOOSE HEADER STYLE</div>
  <div class="option-label" style="left:326px;top:561px">01 - Light Blue Gradient Only</div>
  <div class="option-label" style="left:879px;top:561px">02 - White Layer + Light Blue Gradient</div>

  <div class="email-hero" style="left:80px;top:609px">
    <div class="top-bar"></div>
    <div class="brand"><span class="brand-mark"></span>Pelmora</div>
    <div class="contact-link">Contact</div>
    <div class="headline">Experiencing KEX Weariness?</div>
    <div class="offer">Unlimited Notice of Assessment Orders<br>For Just <span class="price">$29 / Month</span></div>
    <div class="cta">Get Started Now</div>
    <div class="hero-art has-shadow" role="img" aria-label="White illustration of a tired worker slumped over a desk"></div>
  </div>

  <div class="email-hero has-white-layer" style="left:637px;top:609px">
    <div class="top-bar"></div>
    <div class="brand"><span class="brand-mark"></span>Pelmora</div>
    <div class="contact-link">Contact</div>
    <div class="headline">Experiencing KEX Weariness?</div>
    <div class="offer">Unlimited Notice of Assessment Orders<br>For Just <span class="price">$29 / Month</span></div>
    <div class="cta">Get Started Now</div>
    <div class="hero-art has-shadow" role="img" aria-label="White illustration of a tired worker slumped over a desk"></div>
  </div>

  <!-- Footer style -->
  <div class="section-band" style="top:888px">CHOOSE FOOTER STYLE</div>
  <div class="option-label" style="left:310px;top:955px">01 - Without Image</div>
  <div class="option-label" style="left:880px;top:952px">02 - With Image</div>

  <div class="email-footer footer-plain" style="left:66px;top:998px">
    <div class="about-bar">About Us</div>
    <div class="about-body">
      <p class="about-text">Pelmora provides on-demand administrative support for Mortgage Professionals across Canada. Everything from Notice of Assessment and Title Orders to inbound document sorting and lender fulfilment can be outsouced at a fraction of the cost of a full time administrator.</p>
    </div>
    <div class="legal-bar"><span>© Pelmora 2016 All rights reserved.</span><span>Unsubscribe here</span></div>
  </div>

  <div class="email-footer footer-with-image" style="left:647px;top:993px">
    <div class="about-bar">About Us</div>
    <div class="about-body">
      <div class="about-art" role="img" aria-label="Photo of office filing cabinets in blue tones with the company name"></div>
      <p class="about-text">Pelmora provides on-demand administrative support for Mortgage Professionals across Canada. Everything from Notice of Assessment and Title Orders to inbound document sorting and lender fulfilment can be outsouced at a fraction of the cost of a full time administrator.</p>
    </div>
    <div class="legal-bar"><span>© Pelmora 2016 All rights reserved.</span><span>Unsubscribe here</span></div>
  </div>

</body>
</html>
```